Vantro cards

I am in the auto motive, transportation business I would like a business card that is Something cool, modern edgy, having to do with car culture. I offer towing service for high and exotic cars. I also provide towing for collisions and car accidents. I offer open and enclosed transport nationwide.

Target Market(s)

Car culture people high end auto collectors

Industry/Entity Type

Towing car carrier

Contact Information for Business Card

My company colors black yellow and silver

Font styles to use
Serif

```html
<!DOCTYPE html>
<html lang="en">
<head>
<meta charset="UTF-8">
<title>Vantro Transportation – Business Card</title>
<link href="https://fonts.googleapis.com/css2?family=Alfa+Slab+One&family=Poppins:wght@400;500;600&display=swap" rel="stylesheet">
<style>
  :root {
    --stage: #2a2a2c;
    --card: #1c1d1f;
    --card-back-top: #3a3b3e;
    --card-back-bottom: #121214;
    --yellow: #f5d23c;
    --white: #ffffff;
    --silver: #9a9ca0;
    --ink: #1c1d1f;
  }
  * { box-sizing: border-box; margin: 0; padding: 0; }
  html, body {
    width: 1200px; height: 1108px; overflow: hidden;
    background: var(--stage);
  }
  .sheet {
    position: relative; width: 1200px; height: 1108px;
    display: flex; justify-content: center; align-items: center; gap: 80px;
  }
  .card {
    width: 440px; height: 720px; border-radius: 22px;
    background: var(--card);
    box-shadow: 0 18px 40px rgba(0,0,0,.45);
    position: relative; overflow: hidden;
  }
  .card-front {
    display: flex; flex-direction: column; align-items: center;
    padding-top: 120px; color: var(--white);
    font-family: 'Poppins', sans-serif; text-align: center;
  }
  .brand {
    display: flex; align-items: center; gap: 14px;
    font-family: 'Poppins', sans-serif; font-weight: 600;
    font-size: 50px; letter-spacing: 1px; color: var(--white);
    text-transform: uppercase; line-height: 1.1;
  }
  .brand-dot {
    width: 22px; height: 22px; border-radius: 50%; background: var(--yellow);
  }
  .brand-sub {
    margin-top: 6px; font-family: 'Poppins', sans-serif; font-weight: 600;
    font-size: 18px; letter-spacing: 4px; color: var(--white);
    text-transform: uppercase;
  }
  .holder-name {
    margin-top: 110px; font-family: 'Alfa Slab One', serif; font-weight: 400;
    font-size: 36px; color: var(--yellow); letter-spacing: 1px;
    text-transform: uppercase; line-height: 1;
  }
  .holder-title {
    margin-top: 8px; font-size: 17px; letter-spacing: 1px;
    text-transform: uppercase;
  }
  .icon-row {
    margin-top: 18px; width: 320px;
    display: flex; align-items: center; gap: 10px;
  }
  .rule { flex: 1; height: 1px; background: var(--silver); }
  .icon {
    width: 34px; height: 34px; border-radius: 6px; background: var(--yellow);
    display: flex; align-items: center; justify-content: center;
  }
  .icon svg { width: 20px; height: 20px; }
  .contact-list { margin-top: 10px; font-size: 20px; line-height: 1.4; }
  .divider { margin: 18px 0; width: 320px; height: 1px; background: var(--silver); }
  .address { font-size: 20px; line-height: 1.4; }
  .card-back {
    background: linear-gradient(160deg, var(--card-back-top), var(--card-back-bottom) 70%);
  }
  .pattern-fill { position: absolute; inset: 0; }
  .back-mark {
    position: absolute; left: 0; right: 0; bottom: 150px;
    text-align: center; font-family: 'Poppins', sans-serif; font-weight: 600;
    font-size: 26px; letter-spacing: 2px; color: var(--white);
    text-transform: uppercase;
  }
</style>
</head>
<body>
<main class="sheet">
  <section class="card card-front">
    <div class="brand"><span class="brand-dot"></span>Vantro</div>
    <div class="brand-sub">Transportation</div>

    <h1 class="holder-name">Marcus Hale</h1>
    <p class="holder-title">Managing Director</p>

    <div class="icon-row">
      <span class="rule"></span>
      <span class="icon" aria-label="Phone">
        <svg viewBox="0 0 24 24"><path d="M6.6 10.8a15 15 0 0 0 6.6 6.6l2.2-2.2a1 1 0 0 1 1-.25 11.4 11.4 0 0 0 3.6.6 1 1 0 0 1 1 1V20a1 1 0 0 1-1 1A17 17 0 0 1 3 4a1 1 0 0 1 1-1h3.5a1 1 0 0 1 1 1c0 1.25.2 2.45.6 3.6a1 1 0 0 1-.25 1z" fill="#1c1d1f"/></svg>
      </span>
      <span class="icon" aria-label="Email">
        <svg viewBox="0 0 24 24"><rect x="3" y="6" width="18" height="12" fill="none" stroke="#1c1d1f" stroke-width="2"/><path d="M3 6l9 7 9-7" fill="none" stroke="#1c1d1f" stroke-width="2"/></svg>
      </span>
      <span class="icon" aria-label="Website">
        <svg viewBox="0 0 24 24"><circle cx="12" cy="12" r="8.5" fill="none" stroke="#1c1d1f" stroke-width="2"/><path d="M3.5 12h17M12 3.5c3 3 3 14 0 17M12 3.5c-3 3-3 14 0 17" fill="none" stroke="#1c1d1f" stroke-width="1.6"/></svg>
      </span>
      <span class="rule"></span>
    </div>

    <div class="contact-list">
      <p>055-318 204 667</p>
      <p>hello@vantrohaul.com</p>
      <p>www.vantrohaul.com</p>
    </div>
    <div class="divider"></div>
    <div class="address">
      <p>88, Kessler Ridge Avenue</p>
      <p>60417, United States</p>
    </div>
  </section>

  <section class="card card-back">
    <div class="pattern-fill" role="img" aria-label="Repeating pattern of tow truck silhouettes in glossy black and grey"></div>
    <div class="back-mark">Vantro</div>
  </section>
</main>
</body>
</html>
```